Birchline Septic Solutions

Would like to see some single sided ones but would also like to see some double sided with one sided only being the logo. Owners name is Colin Vandro. Phone number is 555-214-0387
Services are pumping, inspections, installs, and repairs

Contact Information for Business Card

555-241-0387 Colin Vandro Maple Hollow, OH

```html
<!DOCTYPE html>
<html lang="en">
<head>
<meta charset="utf-8">
<title>Birchline Septic Solutions – Business Card</title>
<link rel="stylesheet" href="https://fonts.googleapis.com/css2?family=Montserrat:wght@500;700;800&display=swap">
<style>
  :root {
    --page-bg: #2a2d31;
    --card-black: #1d1d1e;
    --brand-teal: #26b3ad;
    --text-white: #f4f4f4;
  }
  html, body {
    margin: 0;
    padding: 0;
    width: 1200px;
    height: 900px;
    overflow: hidden;
    background: var(--page-bg);
  }
  .canvas {
    width: 1200px;
    height: 900px;
    display: flex;
    align-items: center;
    justify-content: center;
  }
  .business-card {
    position: relative;
    width: 880px;
    height: 500px;
    background: var(--card-black);
    border-radius: 34px;
    box-shadow: 0 18px 40px rgba(0, 0, 0, 0.45);
    display: flex;
    align-items: center;
    font-family: "Montserrat", sans-serif;
  }
  .brand-block {
    width: 390px;
    padding-left: 60px;
    box-sizing: border-box;
    display: flex;
    align-items: center;
    gap: 16px;
  }
  .brand-mark {
    width: 22px;
    height: 22px;
    background: var(--brand-teal);
    flex-shrink: 0;
  }
  .brand-name {
    margin: 0;
    color: var(--text-white);
    font-weight: 700;
    font-size: 24px;
    line-height: 1.3;
    letter-spacing: 0.04em;
    text-transform: uppercase;
    white-space: nowrap;
  }
  .divider {
    width: 2px;
    height: 170px;
    background: var(--brand-teal);
    margin: 0 34px 0 0;
    flex-shrink: 0;
  }
  .contact-block {
    display: flex;
    flex-direction: column;
    gap: 10px;
    white-space: nowrap;
  }
  .owner-name {
    margin: 0;
    color: var(--brand-teal);
    font-weight: 800;
    font-size: 42px;
    letter-spacing: 0.02em;
    text-transform: uppercase;
    line-height: 1.1;
  }
  .location {
    margin: 0;
    color: var(--text-white);
    font-weight: 500;
    font-size: 26px;
  }
  .phone {
    margin: 14px 0 0;
    display: flex;
    align-items: center;
    gap: 12px;
    color: var(--text-white);
    font-weight: 500;
    font-size: 38px;
    letter-spacing: 0.01em;
  }
  .phone-icon {
    width: 28px;
    height: 28px;
    fill: var(--brand-teal);
  }
</style>
</head>
<body>
  <main class="canvas">
    <section class="business-card" aria-label="Business card">
      <div class="brand-block">
        <span class="brand-mark" aria-hidden="true"></span>
        <p class="brand-name">Birchline<br>Septic Solutions</p>
      </div>
      <div class="divider" aria-hidden="true"></div>
      <div class="contact-block">
        <h1 class="owner-name">Colin Vandro</h1>
        <p class="location">Maple Hollow, OH</p>
        <p class="phone">
          <svg class="phone-icon" viewBox="0 0 24 24" aria-hidden="true">
            <path d="M6.6 10.8a15.1 15.1 0 0 0 6.6 6.6l2.2-2.2a1 1 0 0 1 1-.25 11.4 11.4 0 0 0 3.6.57 1 1 0 0 1 1 1V20a1 1 0 0 1-1 1A17 17 0 0 1 3 4a1 1 0 0 1 1-1h3.5a1 1 0 0 1 1 1c0 1.25.2 2.45.57 3.57a1 1 0 0 1-.25 1z"/>
          </svg>
          555-241-0387
        </p>
      </div>
    </section>
  </main>
</body>
</html>
```